Plimsy Salve by Tiny Wrens: All Natural Lip Balm Co. Looking for New Label

Greetings, our company is called Tiny Wrens and we are a start-up founded in early 2014. We make 100% All-Natural lip balm, called Plimsy Salve, in a variety of flavors and we are looking for a new label that incorporates part of our logo and highlights our product name and our lip balms flavor (see attached files). Our website is: plimsysalve.example, and we are on Twitter: @TinyWrensSalves, and Facebook: /TinyWrensSalves. Our lip balms are made with beeswax, sweet almond oil, shea butter, coconut oil and other all natural oils and flavors.

The design should be clean, and communicate comfort, its "all-natural-ness", reliability, and fun. The colors we would like to have incorporated are burgundy, a deep, but not dark orange (see files, website, logo, graphics), some green and maybe gold/yellow. Given that the lip balm tubes are small (standard tubes), we would like to assure that the lip balm name, the flavor, and part of the logo- (perhaps the bee), are clearly visible and easily read. I am open to a variety of fonts, as long as they convey what I have stated above.

We want to use the label graphics and our logo for not only labeling our product, but also for use on our website, on banners, signs, retail boxes, letterhead, tee shirts, etc. If we like the design we are open to working with you again as our company is growing and we will be expanding our product line within the year to include hand and body balms, as well as other similar items and we will eventually have a few different product lines marketed at various age groups as well. Our lip balm is currently marketed to 14 to 40+ demographic, with the average age being roughly in the 15 to 24 range and our lip balm has been purchased by more women than men, though we market to both.

As far as software goes, I would like it to be in a format that is most popular- my old logo and graphics were made in Adobe Creative Suite 5.0, Adobe InDesign, and Adobe Illustrator, so the label should be made using this software (or a higher version). If I can have the label in a JPEG format also so I personally can add it to my website and social media that would be great.

I have a label redesign doc in an indd format but it was too large to upload. I believe this was the entire layout of our last label. If you need this, or anything else, please let me know as well as how I can send it to you.

We have applied to the popular TV show Otter Pond and recently received a call back with interest from the producers; we are so excited and hope you are as well!

Thank you!
Todd Vaselko
Owner
Tiny Wrens Salves LLC
Todd@TinyWrensSalves.example

The Label dimensions are: 2.25 inches wide ---> by 2 inches long. Currently, there is a .75 inch area that is part of the label and is perforated, used as a safety seal. I may be changing the labels to a slightly different kind but the dimensions will be the same. The tubes we use are standard lip balm tubes with a net weight of .15 ounces ( the total length of the tube from the bottom turning piece to the top of the cap is just over 2.5 inches (this is NOT how large the label must be).We are discontinuing the 1 Hive, 2 Hive concepts ( for different consistencies of the balm) so that part of the label does not need to be included.Feel free to enhance and/or modify the logo to fit the design of the label.Thank you! Added Thursday, February 12, 2015

Industry/Entity Type

Software

Requirements
Must have
• Label Dimensions:
• Length: 2.125" Height: 2.125"
• Top Margin: 1.025" Bottom Margin: 1.025"
• Left Margin: 0.9125" Right Margin: 0.9125"
• Horizontal Spacing: 0.15" Vertical Spacing: 0.15"
• Horizontal Pitch: 2.275" Vertical Pitch: 2.275"

```html
<!DOCTYPE html>
<html lang="en">
<head>
<meta charset="utf-8">
<title>Plimsy Salve – Citrus Cloudpuff lip balm labels</title>
<link href="https://fonts.googleapis.com/css2?family=Poiret+One&family=Open+Sans:wght@400;600&display=swap" rel="stylesheet">
<style>
  :root {
    --paper: #ffffff;
    --honey-light: #fde3bd;
    --honey: #f8c27a;
    --orange: #ff6a00;
    --orange-frame: #f39a1e;
    --blush: #ffd4cf;
    --leaf: #5cf22a;
    --burgundy: #a3173a;
    --ink: #4a4a4a;
    --bee-gold: #f5a534;
    --bee-dark: #2b2b2b;
  }
  * { box-sizing: border-box; margin: 0; padding: 0; }
  html, body { width: 1200px; height: 669px; overflow: hidden; background: var(--paper); }
  .canvas { position: relative; width: 1200px; height: 669px; background: var(--paper); }

  .label { position: absolute; top: 80px; width: 544px; height: 486px; overflow: hidden; }
  .label--honey { left: 62px; border: 2px solid var(--honey-light); }
  .label--stripes { left: 655px; border: 2px solid var(--orange-frame); background: var(--paper); }

  .honeycomb-fill {
    position: absolute; inset: 0;
    background: radial-gradient(circle at 30% 30%, var(--honey) 0%, var(--honey-light) 55%, var(--honey) 100%);
  }

  .band { position: absolute; }
  .band--full { left: 0; right: 0; height: 46px; background: var(--orange); }
  .band--block { height: 47px; }
  .band--orange { background: var(--orange); }
  .band--blush { background: var(--blush); }

  .perforation {
    position: absolute; top: 0; bottom: 0; width: 0;
    border-left: 3px dashed #111;
  }

  .front-panel { position: absolute; text-align: center; }
  .label--honey .front-panel { left: 54px; top: 105px; width: 248px; height: 268px; background: var(--paper); border: 3px solid var(--orange); }
  .label--stripes .front-panel { left: 56px; top: 105px; width: 238px; height: 263px; background: var(--orange); }

  .bee-art {
    position: absolute; left: 4px; top: -12px; width: 208px; height: 160px;
    border-radius: 40% 50% 45% 40%;
    background: linear-gradient(135deg, #c9f5c0 0%, var(--bee-gold) 45%, var(--bee-dark) 100%);
    opacity: .85;
  }

  .product-name {
    position: absolute; left: 0; right: 0; top: 172px;
    font-family: "Poiret One", sans-serif; font-size: 42px; font-weight: 400; line-height: 1;
    white-space: nowrap;
  }
  .flavor {
    position: absolute; left: 0; right: 0; top: 222px;
    font-family: "Poiret One", sans-serif; font-size: 20px; line-height: 1;
    white-space: nowrap;
  }
  .descriptor {
    position: absolute; left: 0; right: 0; top: 245px;
    font-family: "Open Sans", sans-serif; font-size: 11.5px; font-weight: 600; line-height: 1;
  }
  .label--honey .product-name { color: var(--leaf); }
  .label--honey .flavor { color: var(--orange); }
  .label--honey .descriptor { color: var(--ink); }
  .label--stripes .product-name,
  .label--stripes .flavor,
  .label--stripes .descriptor { color: var(--paper); }

  .seal-panel { position: absolute; }
  .label--honey .seal-panel { left: 420px; top: 104px; width: 74px; height: 265px; background: var(--paper); border: 3px solid var(--orange); }
  .label--stripes .seal-panel { left: 423px; top: 107px; width: 68px; height: 260px; background: var(--orange); }

  .seal-text {
    position: absolute; right: 6px; top: 8px;
    writing-mode: vertical-rl;
    font-family: "Poiret One", sans-serif; line-height: 1.05;
    white-space: nowrap;
  }
  .seal-name { display: block; font-size: 29px; }
  .seal-flavor { display: block; font-size: 14px; padding-top: 2px; }
  .label--honey .seal-name { color: var(--burgundy); }
  .label--honey .seal-flavor { color: var(--orange); }
  .label--stripes .seal-name,
  .label--stripes .seal-flavor { color: var(--paper); }

  .flight-path { position: absolute; left: 16px; top: 180px; width: 30px; height: 50px; }
  .mini-bee {
    position: absolute; left: 16px; top: 220px; width: 34px; height: 30px;
    border-radius: 45%;
    background: linear-gradient(135deg, #c9f5c0 0%, var(--bee-gold) 50%, var(--bee-dark) 100%);
  }
</style>
</head>
<body>
<main class="canvas">

  <section class="label label--honey" aria-label="Lip balm label, honeycomb version">
    <div class="honeycomb-fill" role="img" aria-label="Honeycomb hexagon pattern in soft honey tones"></div>
    <div class="perforation" style="left:361px"></div>

    <div class="front-panel">
      <div class="bee-art" role="img" aria-label="Cartoon bee mascot with green wings"></div>
      <h1 class="product-name">Plimsy Salve</h1>
      <p class="flavor">Citrus Cloudpuff</p>
      <p class="descriptor">beewax lip balm</p>
    </div>

    <div class="seal-panel">
      <p class="seal-text"><span class="seal-name">Plimsy Salve</span><span class="seal-flavor">Citrus Cloudpuff</span></p>
      <svg class="flight-path" viewBox="0 0 30 50" aria-hidden="true"><path d="M22 0 C 24 14, 6 18, 12 32 S 20 44, 18 50" fill="none" stroke="#222" stroke-width="1.5" stroke-dasharray="3 3"/></svg>
      <div class="mini-bee" role="img" aria-label="Small bee mascot"></div>
    </div>
  </section>

  <section class="label label--stripes" aria-label="Lip balm label, striped version">
    <div class="band band--full" style="top:24px"></div>
    <div class="band band--full" style="top:409px"></div>

    <div class="band band--block band--blush" style="top:121px; left:0; width:55px"></div>
    <div class="band band--block band--blush" style="top:121px; left:298px; width:62px"></div>
    <div class="band band--block band--blush" style="top:121px; left:495px; width:49px"></div>

    <div class="band band--block band--orange" style="top:215px; left:0; width:55px"></div>
    <div class="band band--block band--orange" style="top:215px; left:298px; width:62px"></div>
    <div class="band band--block band--orange" style="top:215px; left:495px; width:49px"></div>

    <div class="band band--block band--blush" style="top:312px; left:0; width:55px"></div>
    <div class="band band--block band--blush" style="top:312px; left:298px; width:62px"></div>
    <div class="band band--block band--blush" style="top:312px; left:495px; width:49px"></div>

    <div class="perforation" style="left:361px"></div>

    <div class="front-panel">
      <div class="bee-art" role="img" aria-label="Cartoon bee mascot with green wings"></div>
      <h2 class="product-name">Plimsy Salve</h2>
      <p class="flavor">Citrus Cloudpuff</p>
      <p class="descriptor">beewax lip balm</p>
    </div>

    <div class="seal-panel">
      <p class="seal-text"><span class="seal-name">Plimsy Salve</span><span class="seal-flavor">Citrus Cloudpuff</span></p>
      <svg class="flight-path" viewBox="0 0 30 50" aria-hidden="true"><path d="M22 0 C 24 14, 6 18, 12 32 S 20 44, 18 50" fill="none" stroke="#ffffff" stroke-width="1.5" stroke-dasharray="3 3"/></svg>
      <div class="mini-bee" role="img" aria-label="Small bee mascot"></div>
    </div>
  </section>

</main>
</body>
</html>
```